KBT Business Cards

We require business cards for our business. We would like a matte black back to the card, with our logo centred in the middle. The front side of the card is open to design.

Target Market(s)

Clients looking for legal services (professional)

Industry/Entity Type

Legal

Contact Information for Business Card

Doran Kelbrath
Partner
Mobile: 0461 738 524
Email: doran@kbtlaw.co
Website: www.kbtlaw.co
Level 3, 118 Wendmore Street
Sydney NSW 2000

Font styles to use
Other font styles liked:
• Avenir

Colors
f04a50
ffffff
1b1b1b

Requirements
Must have
• Black back with logo included in the centre of the card.
• Our font is Avenir.

```html
<!DOCTYPE html>
<html lang="en">
<head>
<meta charset="utf-8">
<title>KBT Legal – Business Cards</title>
<link href="https://fonts.googleapis.com/css2?family=Nunito+Sans:wght@400;600;700&display=swap" rel="stylesheet">
<style>
  :root {
    --backdrop: #e4e4e4;
    --card-black: #1b1b1b;
    --brand-red: #d21f47;
    --brand-red-deep: #a8143a;
    --white: #ffffff;
    --muted: #bdbdbd;
  }
  * { box-sizing: border-box; margin: 0; padding: 0; }
  html, body {
    width: 1200px; height: 675px; overflow: hidden;
    background: var(--backdrop);
    font-family: "Nunito Sans", "Avenir", sans-serif;
  }
  .canvas {
    position: relative; width: 1200px; height: 675px;
    display: flex; align-items: center; justify-content: center; gap: 40px;
  }
  .card {
    position: relative; width: 520px; height: 297px; overflow: hidden;
    box-shadow: 0 10px 24px rgba(0,0,0,.22);
  }
  .card-shape { position: absolute; inset: 0; width: 100%; height: 100%; }

  /* Front */
  .contact {
    position: absolute; left: 30px; bottom: 34px;
    color: var(--white); font-size: 14px; line-height: 1.45;
  }
  .contact-row { display: flex; align-items: center; gap: 9px; }
  .contact-row svg { width: 12px; height: 12px; flex: none; }
  .contact-row strong { font-weight: 700; }
  .address { margin-top: 10px; font-size: 15px; line-height: 1.3; }
  .front-mark {
    position: absolute; left: 300px; top: 92px;
    display: flex; align-items: center; gap: 10px;
  }
  .mark-square { width: 22px; height: 22px; background: var(--brand-red); }
  .mark-name {
    color: var(--white); font-weight: 700; font-size: 30px; letter-spacing: 2px;
  }
  .holder {
    position: absolute; left: 224px; top: 170px;
    color: var(--white); font-size: 17px; letter-spacing: .5px;
    display: flex; align-items: center; gap: 7px;
  }
  .holder-name { font-weight: 600; }
  .holder-divider { width: 1.5px; height: 20px; background: var(--white); }
  .holder-role { font-weight: 400; font-size: 15px; }

  /* Back */
  .card-back { background: var(--card-black); }
  .back-mark {
    position: absolute; left: 50%; top: 50%; transform: translate(-50%, -50%);
    display: flex; align-items: center; gap: 14px;
  }
  .back-mark .mark-square { width: 28px; height: 28px; }
  .back-mark .mark-name { font-size: 36px; letter-spacing: 3px; }
  .back-web {
    position: absolute; right: 30px; bottom: 24px;
    color: var(--muted); font-size: 12px; letter-spacing: .5px;
  }
</style>
</head>
<body>
<main class="canvas">
  <section class="card card-front" aria-label="Business card front">
    <svg class="card-shape" viewBox="0 0 520 297" preserveAspectRatio="none" aria-hidden="true">
      <defs>
        <linearGradient id="redPanel" x1="0" y1="0" x2="1" y2="1">
          <stop offset="0" stop-color="var(--brand-red)"/>
          <stop offset="1" stop-color="var(--brand-red-deep)"/>
        </linearGradient>
      </defs>
      <rect width="520" height="297" fill="url(#redPanel)"/>
      <path d="M168 0 H520 V297 H336 Q250 150 168 0 Z" fill="var(--card-black)"/>
      <path d="M196 178 Q250 230 292 297 H312 Q262 226 196 178 Z" fill="var(--card-black)"/>
    </svg>

    <div class="front-mark">
      <span class="mark-square"></span>
      <span class="mark-name">KBT</span>
    </div>

    <div class="holder">
      <span class="holder-name">DORAN KELBRATH</span>
      <span class="holder-divider"></span>
      <span class="holder-role">Partner</span>
    </div>

    <div class="contact">
      <div class="contact-row">
        <svg viewBox="0 0 12 12" aria-hidden="true"><path d="M2.5 1 L4.5 1 L5.2 3.4 L3.9 4.4 Q5 6.8 7.6 8.1 L8.6 6.8 L11 7.5 L11 9.5 Q10.5 11 9 11 Q1 10 1 3 Q1 1.5 2.5 1 Z" fill="currentColor"/></svg>
        <span>0461 738 524</span>
      </div>
      <div class="contact-row">
        <svg viewBox="0 0 12 12" aria-hidden="true"><rect x="1" y="2.5" width="10" height="7" fill="none" stroke="currentColor" stroke-width="1.2"/><path d="M1 2.5 L6 6.5 L11 2.5" fill="none" stroke="currentColor" stroke-width="1.2"/></svg>
        <span>doran@kbtlaw.co</span>
      </div>
      <div class="contact-row">
        <svg viewBox="0 0 12 12" aria-hidden="true"><circle cx="6" cy="6" r="4.8" fill="none" stroke="currentColor" stroke-width="1.1"/><ellipse cx="6" cy="6" rx="2" ry="4.8" fill="none" stroke="currentColor" stroke-width="1"/><path d="M1.2 6 H10.8" stroke="currentColor" stroke-width="1"/></svg>
        <span>www.<strong>kbtlaw.co</strong></span>
      </div>
      <p class="address">Level 3, 118 Wendmore Street<br>Sydney NSW 2000</p>
    </div>
  </section>

  <section class="card card-back" aria-label="Business card back">
    <div class="back-mark">
      <span class="mark-square"></span>
      <span class="mark-name">KBT LEGAL</span>
    </div>
    <p class="back-web">www.kbtlaw.co</p>
  </section>
</main>
</body>
</html>
```